Webdesign für Bedrucken Papiertaschen, Schildern etc.
Zielgruppe
Wir bedrucken Papiertaschen, Papierbeutel, Laternen, Aluplaketten, Schilder, etc. und lasern Hundemarken. Zielgruppen von Privat bis Geschäftskunden
Aufgabenstellung
Der Shop sollte ein einfacher und kostengünstiger 'web2print'-shop werden. Wo die Kunden anhand von einem Editor Ihre Logos oder Druckvorlagen selber hochladen und/oder gestalten könne. Bisher haben die Kunden eifach ihre Bidldatei per E-Mail geschickt und wir haben diese dann weiter verarbeit.
Der Shop sollte, wenn möglich, günstig im Unterhalt sein, da wir nicht abschätzen können, wie gut diese laufen wird.
Wir haben wie 3 Bereich: 1. Papierbeutel/Taschen / 2. Stallplaketten (für z.B. Pferdesport) / 3. Diverses (Wie z.B. die Laternen, Schilder, Hundemarken, etc.)
Es würde sich um eine separate Webseite handeln. Daher ist bei Design freie Hand, eifach und klar... auch für nicht so ambitionierte Privatkunden oder kleine Unternehmen.

```html
<!DOCTYPE html>
<html lang="de">
<head>
<meta charset="utf-8">
<title>Taschenwerk – Individuelle Druck- &amp; Lasergravur</title>
<link href="https://fonts.googleapis.com/css2?family=Poppins:wght@300;400;500;600;700&family=Inter:wght@300;400;500&display=swap" rel="stylesheet">
<style>
:root{
  --ink:#0b0b0b;
  --paper:#ffffff;
  --muted:#6e6e6e;
  --line:#e6e6e6;
  --accent:#8a5a2b;
  --number:#555555;
  --star:#f07a5a;
  --hero-b:#d9bf9c;
}
*{box-sizing:border-box;margin:0;padding:0}
html,body{width:1200px;height:3306px;overflow:hidden;background:var(--paper)}
body{font-family:"Poppins",sans-serif;color:var(--ink);position:relative}
a{color:inherit;text-decoration:none}

/* nav */
.nav{position:absolute;left:0;top:0;width:1200px;height:73px}
.brand{position:absolute;left:42px;top:22px;font:700 19px/1 "Poppins",sans-serif;letter-spacing:-.3px}
.nav-link{position:absolute;top:26px;font:400 15px/1 "Poppins",sans-serif;color:#555}
.nav-link.active{color:var(--ink);font-weight:600;text-decoration:underline;text-underline-offset:4px}
.cart{position:absolute;left:1138px;top:24px}

/* hero (all positions relative to the hero box, which starts at y=73) */
.hero{position:absolute;left:0;top:73px;width:1200px;height:735px;border-radius:0 10px 10px 10px;overflow:hidden;
  background:linear-gradient(90deg,#f6f2ec 0%,#f3ede5 38%,#e7d5bd 58%,var(--hero-b) 78%,#c9a57b 100%)}
.hero-photo{position:absolute;left:470px;top:0;width:730px;height:735px;
  background:radial-gradient(ellipse at 60% 45%,rgba(255,248,236,.55),rgba(0,0,0,0) 60%),
  linear-gradient(180deg,rgba(0,0,0,0) 70%,rgba(140,106,68,.45) 100%)}
.eyebrow{position:absolute;left:67px;top:82px;font:500 16px/1 "Poppins",sans-serif;letter-spacing:.6px;color:var(--accent)}
.eyebrow-rule{position:absolute;left:67px;top:114px;width:49px;height:2px;background:var(--accent)}
.hero-title{position:absolute;left:65px;top:138px;font:600 70px/77px "Poppins",sans-serif;letter-spacing:-1.5px;white-space:nowrap}
.hero-text{position:absolute;left:67px;top:308px;width:410px;font:400 18.5px/29px "Inter",sans-serif;color:#333}
.btn{position:absolute;display:flex;align-items:center;justify-content:center;gap:10px;font:500 15px/1 "Poppins",sans-serif;border-radius:4px;white-space:nowrap}
.btn-dark{background:var(--ink);color:#fff}
.btn-outline{border:1.5px solid var(--ink);color:var(--ink);background:rgba(255,255,255,.4)}
.feature{position:absolute;top:530px;width:110px;text-align:center;font:400 12.5px/17px "Poppins",sans-serif}
.feature svg{display:block;margin:0 auto 12px}

/* sections */
.section-title{position:absolute;left:0;width:1200px;text-align:center;font:600 41px/1 "Poppins",sans-serif;letter-spacing:-.3px}

.product{position:absolute;top:1014px;width:359px;height:503px;border:1.5px solid var(--line);background:#fff}
.product-img{position:absolute;left:32px;top:25px;width:295px;height:244px;border-radius:4px}
.product h3{position:absolute;left:32px;top:290px;font:500 19px/1.2 "Poppins",sans-serif}
.product p{position:absolute;left:32px;top:325px;width:290px;font:400 15px/22px "Poppins",sans-serif;color:#222}
.product .shop{position:absolute;left:32px;top:444px;width:295px;height:43px;background:var(--ink);color:#fff;
  display:flex;align-items:center;justify-content:center;font:400 15px/1 "Poppins",sans-serif;border-radius:2px}

.step{position:absolute;top:1726px;width:361px;height:256px;background:#fff;border:1.5px solid var(--line);
  box-shadow:0 3px 8px rgba(0,0,0,.08);border-radius:3px;overflow:hidden}
.step-num{position:absolute;right:-4px;top:-16px;font:700 94px/1 "Poppins",sans-serif;color:var(--number);letter-spacing:-2px}
.step-icon{position:absolute;left:50%;top:68px;width:83px;height:83px;margin-left:-41px;border-radius:50%;background:var(--ink);
  display:flex;align-items:center;justify-content:center}
.step h3{position:absolute;left:0;top:192px;width:100%;text-align:center;font:600 21px/1.2 "Poppins",sans-serif}

.review{position:absolute;top:2200px;width:317px;height:215px;background:#fff;border-radius:10px;
  box-shadow:0 14px 34px rgba(0,0,0,.1),0 2px 6px rgba(0,0,0,.06)}
.quote-badge{position:absolute;left:24px;top:-24px;width:46px;height:46px;border-radius:50%;background:var(--ink);
  display:flex;align-items:center;justify-content:center}
.stars{position:absolute;left:24px;top:48px;color:var(--star);font-size:14px;letter-spacing:3px}
.review p{position:absolute;left:24px;top:76px;width:272px;font:300 13.5px/20px "Inter",sans-serif;color:#8a8a8a}
.review hr{position:absolute;left:0;top:152px;width:100%;border:0;border-top:1px solid #eeeeee}
.avatar{position:absolute;left:24px;top:168px;width:29px;height:29px;border-radius:50%;background:#c9c4bf}
.person{position:absolute;left:64px;top:170px;font:400 12px/1.2 "Inter",sans-serif;color:#222}
.person small{display:block;font-size:10px;color:#999}

.cta{position:absolute;left:0;top:2521px;width:1200px;height:338px;background:var(--ink);color:#fff;text-align:center}
.cta h2{position:absolute;left:0;top:64px;width:100%;font:600 41px/1 "Poppins",sans-serif}
.cta p{position:absolute;left:0;top:128px;width:100%;font:400 24px/35px "Poppins",sans-serif}
.cta a{position:absolute;left:455px;top:236px;width:290px;height:43px;background:#fff;color:var(--ink);border-radius:3px;
  display:flex;align-items:center;justify-content:center;font:500 15px/1 "Poppins",sans-serif}

.footer{position:absolute;left:0;top:2964px;width:1200px;height:342px;background:var(--ink);color:#fff}
.footer .rule{position:absolute;left:60px;width:1079px;height:1px;background:#444}
.footer h4{position:absolute;top:66px;font:600 19px/1 "Poppins",sans-serif}
.footer .about{position:absolute;left:122px;top:116px;width:470px;font:400 20px/30px "Poppins",sans-serif}
.footer .links{position:absolute;top:108px;list-style:none;font:400 15px/1 "Poppins",sans-serif;white-space:nowrap}
.footer .links li{height:33.5px}
.copy{position:absolute;left:0;top:302px;width:1200px;text-align:center;font:400 11px/1 "Poppins",sans-serif}
.social{position:absolute;top:294px;width:30px;height:30px;border:1.5px solid #fff;border-radius:5px}
</style>
</head>
<body>

<header class="nav">
  <a class="brand" href="#">taschenwerk</a>
  <a class="nav-link active" href="#" style="left:685px">Startseite</a>
  <a class="nav-link" href="#" style="left:808px">Products</a>
  <a class="nav-link" href="#" style="left:924px">Über uns</a>
  <a class="nav-link" href="#" style="left:1039px">Kintakt</a>
  <svg class="cart" width="22" height="22" viewBox="0 0 24 24" fill="none" stroke="#222" stroke-width="1.6" stroke-linecap="round" stroke-linejoin="round"><path d="M2 3h3l2.5 12h11l2-8H6.2"/><circle cx="9" cy="19.5" r="1.3"/><circle cx="17" cy="19.5" r="1.3"/></svg>
</header>

<section class="hero">
  <div class="hero-photo" role="img" aria-label="Produktfoto: bedruckte Papiertaschen, schwarze Laterne mit Blattmuster, Aluplakette, grüne Stallplakette und gravierte Hundemarke auf Holztisch"></div>
  <div class="eyebrow">INDIVIDUELLE DRUCK- &amp; LASERGRAVUR</div>
  <div class="eyebrow-rule"></div>
  <h1 class="hero-title">Ihr Design.<br>Perfekt Gedruckt.</h1>
  <p class="hero-text">Laden Sie Ihr Logo hoch oder gestalten Sie Ihr Design – wir bringen es auf hochwertige Taschen, Schilder, Schilder und mehr.</p>
  <a class="btn btn-dark" href="#" style="left:67px;top:424px;width:190px;height:52px">
    <svg width="20" height="20" viewBox="0 0 24 24" fill="none" stroke="#fff" stroke-width="1.8" stroke-linecap="round" stroke-linejoin="round"><path d="M11 4H5a1 1 0 0 0-1 1v14a1 1 0 0 0 1 1h14a1 1 0 0 0 1-1v-6"/><path d="M18 2.5l3.5 3.5L12 15.5H8.5V12z"/></svg>
    DESIGN STARTEN</a>
  <a class="btn btn-outline" href="#" style="left:273px;top:424px;width:199px;height:52px">
    <svg width="20" height="20" viewBox="0 0 24 24" fill="none" stroke="#111" stroke-width="1.8" stroke-linecap="round" stroke-linejoin="round"><path d="M4 8h16l-1 13H5z"/><path d="M8.5 8V6a3.5 3.5 0 0 1 7 0v2"/></svg>
    PRODUKTE ANSEHEN</a>

  <div class="feature" style="left:48px">
    <svg width="34" height="36" viewBox="0 0 24 26" fill="none" stroke="#222" stroke-width="1.4" stroke-linecap="round" stroke-linejoin="round"><circle cx="12" cy="9" r="7"/><circle cx="12" cy="9" r="4"/><path d="M8 15l-2 9 6-3 6 3-2-9"/></svg>
    Hochwertiger<br>Druck</div>
  <div class="feature" style="left:149px">
    <svg width="34" height="36" viewBox="0 0 24 26" fill="none" stroke="#222" stroke-width="1.4" stroke-linecap="round" stroke-linejoin="round"><path d="M11 5H4v17h16v-7"/><path d="M18 2.5l3 3-9 9H9v-3z"/></svg>
    Einfacher<br>Design-Editor</div>
  <div class="feature" style="left:248px">
    <svg width="40" height="36" viewBox="0 0 28 26" fill="none" stroke="#222" stroke-width="1.4" stroke-linecap="round" stroke-linejoin="round"><path d="M2 6h15v12H2z"/><path d="M17 10h5l4 4v4h-9"/><circle cx="7" cy="20" r="2"/><circle cx="21" cy="20" r="2"/></svg>
    Schnelle<br>Produktion</div>
  <div class="feature" style="left:349px">
    <svg width="40" height="36" viewBox="0 0 28 26" fill="none" stroke="#222" stroke-width="1.4" stroke-linecap="round" stroke-linejoin="round"><circle cx="14" cy="7" r="4"/><path d="M6 22c0-5 3.5-8 8-8s8 3 8 8z"/><circle cx="5.5" cy="10" r="2.5"/><circle cx="22.5" cy="10" r="2.5"/><path d="M1.5 20c0-3 1.5-5 4-5M26.5 20c0-3-1.5-5-4-5"/></svg>
    Für Unternehmen<br>&amp; Privatpersonen</div>
</section>

<h2 class="section-title" style="top:922px">Unsere Produkte</h2>

<article class="product" style="left:32px">
  <div class="product-img" role="img" aria-label="Produktfoto: zwei bedruckte Kraftpapier-Standbodenbeutel für Tierfutter" style="background:linear-gradient(135deg,#e2dccd,#cfc3a6 55%,#b9ab8c)"></div>
  <h3>Verpackung für Tierfutter</h3>
  <p>Premium kraft paper pouches for pet food products. Features detailed ingredient information and resealable closure.</p>
  <a class="shop" href="#">Jetzt einkaufen</a>
</article>

<article class="product" style="left:421px">
  <div class="product-img" role="img" aria-label="Produktfoto: ovale weiße Erinnerungsplakette für einen Patrouillenritt" style="background:radial-gradient(ellipse at 50% 50%,#f4f3f0 0%,#e7e5e0 45%,#ffffff 72%)"></div>
  <h3>Event-Beschilderung</h3>
  <p>Premium-Kraftpapierbeutel für Tierfutterprodukte. Mit detaillierten Zutateninformationen und wiederverschließbarem Verschluss.</p>
  <a class="shop" href="#" style="font-weight:600">Jetzt einkaufen</a>
</article>

<article class="product" style="left:808px">
  <div class="product-img" role="img" aria-label="Produktfoto: weiße und schwarze Zunftlaternen mit farbigen Wappen" style="left:14px;top:13px;width:330px;height:266px;background:linear-gradient(180deg,#f2f2f2 0%,#e4e4e4 50%,#bdbdbd 100%)"></div>
  <h3 style="top:298px">Individuelle Laterne</h3>
  <p style="top:333px">Traditionelle Zunftlaternen mit individuellem Wappen und Designs. Erhältlich in mehreren Größen.</p>
  <a class="shop" href="#" style="left:34px;width:292px">Jetzt einkaufen</a>
</article>

<h2 class="section-title" style="top:1631px">So funktioniert es</h2>

<div class="step" style="left:37px">
  <div class="step-num">01</div>
  <div class="step-icon"><svg width="42" height="42" viewBox="0 0 24 24" fill="none" stroke="#fff" stroke-width="1.2" stroke-linecap="round" stroke-linejoin="round"><rect x="3" y="4" width="18" height="12" rx="1"/><path d="M9 20h6M12 16v4"/><path d="M6 7h8M6 10h5"/><path d="M13 10l4 3-2 .3 1 2-1 .5-1-2-1 1.5z"/></svg></div>
  <h3>Produkt auswählen</h3>
</div>
<div class="step" style="left:420px">
  <div class="step-num">02</div>
  <div class="step-icon"><svg width="40" height="40" viewBox="0 0 24 24" fill="none" stroke="#fff" stroke-width="1.5" stroke-linecap="round" stroke-linejoin="round"><path d="M14 3H7a2 2 0 0 0-2 2v14a2 2 0 0 0 2 2h10a2 2 0 0 0 2-2V8z"/><path d="M14 3v5h5"/><path d="M12 17v-6M9.5 13.5L12 11l2.5 2.5"/></svg></div>
  <h3 style="top:190px">Design hochladen oder erstellen</h3>
</div>
<div class="step" style="left:802px">
  <div class="step-num">03</div>
  <div class="step-icon"><svg width="40" height="40" viewBox="0 0 24 24" fill="none" stroke="#fff" stroke-width="1.5" stroke-linecap="round" stroke-linejoin="round"><path d="M4 8h14l-.5 5M4 8l1 13h8"/><path d="M8 8V6a3 3 0 0 1 6 0v2"/><circle cx="18" cy="18" r="4"/><path d="M16.3 18l1.2 1.2 2.2-2.4"/></svg></div>
  <h3>Bestellung aufgeben</h3>
</div>

<h2 class="section-title" style="top:2090px">Was unsere Kunden sagen</h2>

<div class="review" style="left:97px">
  <div class="quote-badge"><svg width="18" height="14" viewBox="0 0 18 14" fill="#fff"><path d="M0 14V8C0 3.5 2.5 1 6 0l1 2C5 3 4 4.5 4 6.5h3V14zM10 14V8c0-4.5 2.5-7 6-8l1 2c-2 1-3 2.5-3 4.5h3V14z"/></svg></div>
  <div class="stars">★★★★★</div>
  <p>Die Druckqualität hat unsere Erwartungen übertroffen. Die Papierbeutel sahen sehr hochwertig aus und der Bestellprozess .</p>
  <hr>
  <div class="avatar" role="img" aria-label="Kundenfoto"></div>
  <div class="person">Lukas Verden<small>Customer</small></div>
</div>
<div class="review" style="left:441px">
  <div class="quote-badge"><svg width="18" height="14" viewBox="0 0 18 14" fill="#fff"><path d="M0 14V8C0 3.5 2.5 1 6 0l1 2C5 3 4 4.5 4 6.5h3V14zM10 14V8c0-4.5 2.5-7 6-8l1 2c-2 1-3 2.5-3 4.5h3V14z"/></svg></div>
  <div class="stars">★★★★★</div>
  <p>Die Druckqualität hat unsere Erwartungen übertroffen. Die Papierbeutel sahen sehr hochwertig aus und der Bestellprozess .</p>
  <hr>
  <div class="avatar" role="img" aria-label="Kundenfoto" style="top:166px"></div>
  <div class="person" style="top:168px">Jonas Brehm<small>Customer</small></div>
</div>
<div class="review" style="left:785px">
  <div class="quote-badge"><svg width="18" height="14" viewBox="0 0 18 14" fill="#fff"><path d="M0 14V8C0 3.5 2.5 1 6 0l1 2C5 3 4 4.5 4 6.5h3V14zM10 14V8c0-4.5 2.5-7 6-8l1 2c-2 1-3 2.5-3 4.5h3V14z"/></svg></div>
  <div class="stars">★★★★★</div>
  <p>Die Druckqualität hat unsere Erwartungen übertroffen. Die Papierbeutel sahen sehr hochwertig aus und der Bestellprozess .</p>
  <hr>
  <div class="avatar" role="img" aria-label="Kundenfoto" style="top:166px"></div>
  <div class="person" style="top:168px">Mara Lindqvist<small>Customer</small></div>
</div>

<section class="cta">
  <h2>Bereit, loszulegen?</h2>
  <p>Kontaktieren Sie uns noch heute, um Ihre individuellen<br>Verpackungsbedürfnisse zu besprechen.</p>
  <a href="#">Jetzt einkaufen</a>
</section>

<footer class="footer">
  <div class="rule" style="top:34px"></div>
  <h4 style="left:122px">TASCHENWERK</h4>
  <p class="about">Hochwertige individuelle Verpackungen, Plaketten, Schilder und gravierte Produkte, maßgeschneidert für Ihre Marke.</p>
  <h4 style="left:689px">Navigate</h4>
  <ul class="links" style="left:689px"><li>Startseite</li><li>Produkte</li><li>Über uns</li><li>Kontakt</li></ul>
  <h4 style="left:874px">Connect</h4>
  <ul class="links" style="left:874px"><li>Email: info@falkmann-druck.ch</li><li>Phone: +41 XX XXX XX XX</li></ul>
  <div class="rule" style="top:278px"></div>
  <div class="copy">© 2026 Taschenwerk. All rights reserved.</div>
  <span class="social" style="left:1000px" aria-label="Soziales Netzwerk"></span>
  <span class="social" style="left:1042px" aria-label="Soziales Netzwerk"></span>
  <span class="social" style="left:1083px" aria-label="Soziales Netzwerk"></span>
</footer>

</body>
</html>
```